Brightway Haus Inc. Business Card Design

Brightway Haus Inc. is in search of a great clean design for our business cards!

Looking to incorporate our full logo and watermark on side one (however, I am open to having the text and watermark separated within the design.)

On side two, I am looking to have contact information (Name, Position, Phone #, Email, Website (www.thebrightwayhaus.ca). Can have the logo and/or watermark as part of the design if applicable.

Please add tagline "Where Shine Counts" on either side 1 or 2. This tagline can be in a sans serif, serif or cursive font as long as it compliments overall design. Capitalization can be title or sentence case depending on how it fits within the design.

Get creative!! Looking for a clean, crisp, premium design! Looking for a glossy card finish with spot UV features when printed. Cards will also be printed with rounded corners. Standard dimensions (3.5 x 2).

Target Market(s)

B2B - primary clients are business owners or property management corporations. (residential jobs are few and far between)

Industry/Entity Type

Business

Contact Information for Business Card

- clean, crisp design
- double sided
- spot UV accents and glossy finish upon printing
- standard business card size (3.5 x 2) with rounded corners
- please see project description for requirements per side

Font styles to use
Sans Serif

Requirements
Must have
• - adequate bleeds with print ready files
• - cohesive design elements between side 1 & 2
• - spot UV elements (can be on both sides or just one, use your discretion)
• - colour pallet should match the logo file provided
• - incorporate tagline "where shine counts" (this tagline can be in a serif or sans serif font as long as it is complimentary to the overall design.
Nice to have
• - Premium elements with a clean design
Should not have
• - Please omit cartoon or whimsical like designs, think premium.
• - Colours should not stray from the pallet of the provided logo.

```html
<!DOCTYPE html>
<html lang="en">
<head>
<meta charset="utf-8">
<title>Brightway Haus Inc. Business Card</title>
<link rel="stylesheet" href="https://fonts.googleapis.com/css2?family=Open+Sans:wght@700&family=Roboto:wght@400&display=swap">
<style>
  :root {
    --backdrop: #262626;
    --paper: #f3f3f3;
    --teal: #12b3b3;
    --navy: #1c2452;
    --white: #ffffff;
  }
  * { margin: 0; padding: 0; box-sizing: border-box; }
  html, body { width: 1200px; height: 960px; overflow: hidden; background: var(--backdrop); }
  .card {
    position: absolute;
    width: 600px;
    height: 342px;
    border-radius: 22px;
    overflow: hidden;
  }
  .card-front { left: 314px; top: 114px; background: var(--paper); }
  .card-back { left: 311px; top: 472px; background: var(--navy); }
  .colour-field { position: absolute; inset: 0; }
  .brand {
    position: absolute;
    font-family: "Open Sans", sans-serif;
    font-weight: 700;
    letter-spacing: -0.5px;
    white-space: nowrap;
  }
  .card-front .brand { left: 46px; top: 46px; font-size: 32px; color: var(--navy); }
  .holder { position: absolute; left: 45px; top: 114px; font-family: "Open Sans", sans-serif; font-weight: 700; }
  .holder-name { font-size: 20px; color: var(--teal); line-height: 26px; }
  .holder-role { font-size: 14px; color: var(--navy); line-height: 20px; }
  .contact {
    position: absolute;
    right: 24px;
    top: 176px;
    font-family: "Roboto", sans-serif;
    font-size: 14.5px;
    color: var(--white);
    text-align: right;
    line-height: 19px;
  }
  .address { margin-bottom: 10px; }
  .contact-row { display: flex; justify-content: flex-end; align-items: center; gap: 7px; }
  .contact-row svg { width: 14px; height: 14px; fill: var(--white); flex: none; }
  .card-back .brand { right: 38px; top: 254px; font-size: 27px; color: var(--white); }
  .tagline {
    position: absolute;
    right: 38px;
    top: 290px;
    font-family: "Roboto", sans-serif;
    font-size: 15px;
    letter-spacing: 2.2px;
    color: var(--white);
  }
</style>
</head>
<body>

<section class="card card-front" aria-label="Card front">
  <svg class="colour-field" viewBox="0 0 600 342" aria-hidden="true">
    <path d="M0,270 C130,330 250,300 320,200 C380,118 470,92 600,100 L600,342 L0,342 Z" fill="var(--teal)"/>
  </svg>
  <div class="brand">BRIGHTWAY HAUS INC.</div>
  <div class="holder">
    <div class="holder-name">ELENA MARSH</div>
    <div class="holder-role">CEO/FOUNDER</div>
  </div>
  <div class="contact">
    <div class="address">2140 Harbour Street<br>Halifax, Nova Scotia B3K 2P1</div>
    <div class="contact-row">902 555 0148
      <svg viewBox="0 0 24 24"><path d="M6.6 10.8a15 15 0 0 0 6.6 6.6l2.2-2.2a1 1 0 0 1 1-.25 11.4 11.4 0 0 0 3.6.57 1 1 0 0 1 1 1V20a1 1 0 0 1-1 1A17 17 0 0 1 3 4a1 1 0 0 1 1-1h3.5a1 1 0 0 1 1 1c0 1.25.2 2.45.57 3.57a1 1 0 0 1-.25 1z"/></svg>
    </div>
    <div class="contact-row">902 555 0172
      <svg viewBox="0 0 24 24"><path d="M7 1h10a2 2 0 0 1 2 2v18a2 2 0 0 1-2 2H7a2 2 0 0 1-2-2V3a2 2 0 0 1 2-2zm0 3v15h10V4z"/></svg>
    </div>
    <div class="contact-row">902 555 0190
      <svg viewBox="0 0 24 24"><path d="M6 2h12v6H6zM3 9h18a1 1 0 0 1 1 1v7h-4v5H6v-5H2v-7a1 1 0 0 1 1-1zm5 7v4h8v-4z"/></svg>
    </div>
    <div class="contact-row">hello@thebrightwayhaus.ca
      <svg viewBox="0 0 24 24"><path d="M2 5h20v14H2zm2 2v.5l8 5 8-5V7l-8 5z"/></svg>
    </div>
    <div class="contact-row">www.thebrightwayhaus.ca
      <svg viewBox="0 0 24 24"><path d="M12 2a10 10 0 1 0 0 20 10 10 0 0 0 0-20zm-1 17.9A8 8 0 0 1 4.1 11H7v2l2 2v4.9zm6.9-2.5A2 2 0 0 0 16 16h-1v-3a1 1 0 0 0-1-1H8v-2h2a1 1 0 0 0 1-1V7h2a2 2 0 0 0 2-2v-.4a8 8 0 0 1 2.9 12.8z"/></svg>
    </div>
  </div>
</section>

<section class="card card-back" aria-label="Card back">
  <div class="brand">BRIGHTWAY HAUS INC.</div>
  <div class="tagline">Where Shine Counts</div>
</section>

</body>
</html>
```